physical therapy flyer

2 office locations speciality programs - work injury / Motor vehicle accidents - spanish speaking - do not put balance defecits/ fall prevention - Spanish speaking
neck and back pain shoulder pain/ rotator cuff disorder / bursitis
hip pain knee andle and foot pain post operative care including Spine , shoulder , knee , total joint replacement

Meadowlark Physical therapy & Chiropractic
4871 Pinecrest BLvd
dalton heights ny 10592
7185820147
3715 Tillman Parkway
Fernvale NY 10592
7189043218
www.meadowlarkptrehab.com

```html
<!DOCTYPE html>
<html lang="en">
<head>
<meta charset="UTF-8">
<title>Meadowlark Physical Therapy &amp; Chiropractic Flyer</title>
<link rel="stylesheet" href="https://fonts.googleapis.com/css2?family=Poppins:wght@400;500;600;700;800&display=swap">
<style>
  :root {
    --backdrop: #bdbdbd;
    --paper: #ffffff;
    --paper-warm: #f1efec;
    --ink: #0d2410;
    --green: #78bf3f;
    --green-panel: #4aa547;
    --green-deep: #0b2410;
    --green-ring: #cfe5cb;
    --red: #e3002a;
    --white: #ffffff;
    --bone-light: #e6e6e6;
    --bone-dark: #9a9a9a;
  }
  * { box-sizing: border-box; margin: 0; padding: 0; }
  html, body {
    width: 1200px; height: 1022px; overflow: hidden;
    background: var(--backdrop);
    font-family: "Poppins", sans-serif;
    color: var(--ink);
  }
  .flyer {
    position: absolute; left: 220px; top: 19px;
    width: 760px; height: 984px;
    background: var(--paper);
    overflow: hidden;
  }
  .hero-bg {
    position: absolute; left: 0; top: 0; width: 760px; height: 560px;
    background: var(--paper-warm);
  }
  .hero-photo {
    position: absolute; left: 325px; top: 0; width: 435px; height: 330px;
    background: linear-gradient(110deg, #efe9e2 0%, #f3eeea 35%, #e9e4e1 60%, #d8d2cf 85%, #b9aca5 100%);
  }
  .spine-band { position: absolute; left: 0; top: 290px; width: 760px; height: 340px; }
  .brand {
    position: absolute; left: 53px; top: 46px;
    display: flex; align-items: center; gap: 8px;
  }
  .brand-dot { width: 30px; height: 30px; border-radius: 50%; background: var(--ink); }
  .brand-name { font-size: 13px; font-weight: 400; line-height: 16px; color: var(--ink); }
  .title {
    position: absolute; left: 55px; top: 128px;
    font-size: 40px; line-height: 42px; color: var(--ink);
  }
  .title .light { font-weight: 400; }
  .title .bold { font-weight: 700; }
  .title .amp { font-weight: 400; }
  .title .accent { font-weight: 700; color: var(--green); }

  .badge {
    position: absolute; left: 47px; top: 436px; width: 184px; height: 184px;
    border-radius: 50%; background: var(--green-ring);
  }
  .badge-inner {
    position: absolute; left: 12px; top: 12px; width: 160px; height: 160px;
    border-radius: 50%; background: var(--green);
    display: flex; flex-direction: column; align-items: center; justify-content: center;
    text-align: center; padding-top: 18px;
  }
  .badge-title { color: var(--white); font-weight: 700; font-size: 22px; line-height: 25px; }
  .badge-sub { color: var(--ink); font-weight: 400; font-size: 13px; line-height: 16px; margin-top: 8px; }

  .offer { position: absolute; left: 273px; top: 460px; width: 160px; }
  .offer h2 { font-size: 26px; font-weight: 700; line-height: 30px; }
  .offer h2 span { color: var(--green); }
  .offer p { font-size: 14.5px; line-height: 17.5px; font-weight: 400; margin-top: 2px; }

  .banner {
    position: absolute; left: 0; top: 631px; width: 407px; height: 26px;
    background: var(--red); border-radius: 0 13px 13px 0;
    color: var(--white); font-weight: 700; font-size: 13px; line-height: 26px;
    padding-left: 46px; letter-spacing: 0.1px;
  }
  .care-photo {
    position: absolute; left: 0; top: 660px; width: 258px; height: 324px;
    background: linear-gradient(135deg, #f4f1ee 0%, #e8d6c6 40%, #d9b9a0 65%, #eeeae6 100%);
  }
  .location { position: absolute; left: 271px; width: 150px; }
  .location h3 { font-size: 21px; font-weight: 700; line-height: 24px; }
  .address {
    display: flex; gap: 3px; margin-top: 4px;
    font-size: 13px; font-weight: 500; line-height: 16px;
  }
  .address svg { flex: none; margin-top: 2px; }
  .phone {
    display: flex; align-items: center; gap: 6px;
    margin-top: 10px; width: 136px; height: 25px; border-radius: 13px;
    background: var(--green-panel); color: var(--white);
    font-weight: 600; font-size: 16.5px; padding-left: 4px;
  }
  .phone-icon {
    width: 18px; height: 18px; border-radius: 50%; background: var(--green-deep);
    display: flex; align-items: center; justify-content: center;
  }
  .loc-divider {
    position: absolute; left: 271px; top: 807px; width: 136px; height: 2px;
    background: linear-gradient(90deg, #e7e7e7, #f6f6f6);
  }

  .programs-shape { position: absolute; left: 435px; top: 370px; width: 325px; height: 614px; }
  .programs-title {
    position: absolute; left: 457px; top: 393px;
    font-size: 25px; line-height: 28px; font-weight: 600;
  }
  .programs-title .accent { color: var(--green); }
  .programs-title .white { color: var(--white); font-weight: 700; }
  .program-list { position: absolute; left: 490px; top: 0; list-style: none; }
  .program {
    position: absolute; left: 0; width: 250px;
    display: flex; align-items: flex-start; gap: 20px;
    color: var(--white); font-weight: 600; font-size: 14.5px; line-height: 18px;
  }
  .program svg { flex: none; width: 38px; height: 38px; }
  .program strong { color: var(--green-deep); font-weight: 700; }
  .visit { position: absolute; left: 476px; top: 910px; display: flex; align-items: center; gap: 8px; }
  .visit-label { color: var(--white); font-size: 10px; font-weight: 500; letter-spacing: 0.5px; }
  .visit-url {
    width: 234px; height: 25px; line-height: 25px;
    background: var(--green-deep); color: var(--white);
    border-radius: 13px 0 0 13px; padding-left: 11px;
    font-size: 12px; font-weight: 600; letter-spacing: 0.6px;
  }
</style>
</head>
<body>
<main class="flyer">
  <div class="hero-bg"></div>
  <div class="hero-photo" role="img" aria-label="Photo of a clinician in a white coat explaining a spine model to a patient"></div>

  <svg class="spine-band" viewBox="0 0 760 340" role="img" aria-label="Illustration of a grey vertebral column curving across the page">
    <defs>
      <linearGradient id="boneShade" x1="0" y1="0" x2="0" y2="1">
        <stop offset="0" stop-color="#f2f2f2"/>
        <stop offset="0.5" stop-color="#bdbdbd"/>
        <stop offset="1" stop-color="#8e8e8e"/>
      </linearGradient>
    </defs>
    <path d="M0 200 C 90 150, 200 170, 300 140 C 400 110, 480 60, 560 70 C 650 80, 720 110, 760 120 L 760 260 C 720 230, 660 200, 600 210 C 520 230, 460 260, 380 270 C 280 285, 200 300, 120 300 C 70 300, 30 290, 0 285 Z" fill="url(#boneShade)" opacity="0.85"/>
  </svg>

  <div class="brand">
    <span class="brand-dot"></span>
    <p class="brand-name">Meadowlark Physical Therapy,<br>Chiropractic, and Acupuncture</p>
  </div>

  <h1 class="title">
    <span class="light">Meadowlark</span><br>
    <span class="bold">Physical</span><br>
    <span class="bold">Therapy</span> <span class="amp">&amp;</span><br>
    <span class="accent">Chiropractic</span>
  </h1>

  <div class="badge">
    <div class="badge-inner">
      <p class="badge-title">Spanish<br>Speaking</p>
      <p class="badge-sub">SERVICES<br>AVAILABLE</p>
    </div>
  </div>

  <section class="offer">
    <h2>We <span>Offer</span></h2>
    <p>Relief for many discomforts, including neck pain, back pain, arm pain and knee pain.</p>
  </section>

  <div class="banner">COMPREHENSIVE CARE ACROSS TWO LOCATIONS!</div>
  <div class="care-photo" role="img" aria-label="Photo of a therapist stretching a patient's neck and shoulder"></div>

  <section class="location" style="top:676px">
    <h3>DALTON HEIGHTS</h3>
    <p class="address">
      <svg width="10" height="13" viewBox="0 0 10 13"><path d="M5 0a5 5 0 0 0-5 5c0 3.5 5 8 5 8s5-4.5 5-8a5 5 0 0 0-5-5z" fill="#e3002a"/><circle cx="5" cy="5" r="2" fill="#fff"/></svg>
      <span>4871 Pinecrest BLvd dalton heights NY 10592</span>
    </p>
    <p class="phone">
      <span class="phone-icon"><svg width="10" height="10" viewBox="0 0 24 24"><path d="M6.6 10.8a15 15 0 0 0 6.6 6.6l2.2-2.2a1 1 0 0 1 1-.25 11.4 11.4 0 0 0 3.6.57 1 1 0 0 1 1 1V20a1 1 0 0 1-1 1A17 17 0 0 1 3 4a1 1 0 0 1 1-1h3.5a1 1 0 0 1 1 1c0 1.25.2 2.45.57 3.57a1 1 0 0 1-.25 1z" fill="#fff"/></svg></span>
      7185820147
    </p>
  </section>

  <div class="loc-divider"></div>

  <section class="location" style="top:830px">
    <h3>FERNVALE</h3>
    <p class="address">
      <svg width="10" height="13" viewBox="0 0 10 13"><path d="M5 0a5 5 0 0 0-5 5c0 3.5 5 8 5 8s5-4.5 5-8a5 5 0 0 0-5-5z" fill="#e3002a"/><circle cx="5" cy="5" r="2" fill="#fff"/></svg>
      <span>3715 Tillman Parkway Fernvale NY 10592</span>
    </p>
    <p class="phone">
      <span class="phone-icon"><svg width="10" height="10" viewBox="0 0 24 24"><path d="M6.6 10.8a15 15 0 0 0 6.6 6.6l2.2-2.2a1 1 0 0 1 1-.25 11.4 11.4 0 0 0 3.6.57 1 1 0 0 1 1 1V20a1 1 0 0 1-1 1A17 17 0 0 1 3 4a1 1 0 0 1 1-1h3.5a1 1 0 0 1 1 1c0 1.25.2 2.45.57 3.57a1 1 0 0 1-.25 1z" fill="#fff"/></svg></span>
      7189043218
    </p>
  </section>

  <svg class="programs-shape" viewBox="0 0 325 614" aria-hidden="true">
    <path d="M17 50 C 160 50, 230 70, 325 130 L 325 614 L 17 614 Z" fill="#4aa547"/>
    <path d="M0 10 Q0 0 12 0 L 225 45 L 30 140 Q 0 155 0 125 Z" fill="#0b2410"/>
  </svg>

  <h2 class="programs-title"><span class="accent">Specialty</span><br><span class="white">Programs</span></h2>

  <ul class="program-list">
    <li class="program" style="top:518px">
      <svg viewBox="0 0 38 38" fill="none" stroke="#0b2410" stroke-width="1.6"><circle cx="16" cy="7" r="3.5"/><path d="M16 11l-3 11 6 5-2 9M13 22l-5 14M14 14l9 2M28 10h8v7h-8z"/></svg>
      <span>Work Injuries</span>
    </li>
    <li class="program" style="top:562px">
      <svg viewBox="0 0 38 38" fill="none" stroke="#0b2410" stroke-width="1.6"><path d="M4 28v-7l4-8h18l4 8v7zM4 28v4h5v-4M25 28v4h5v-4M4 21h26"/><circle cx="10" cy="24" r="1.5"/><circle cx="24" cy="24" r="1.5"/><path d="M31 5l2 5 4-2-2 5"/></svg>
      <span>Motor Vehicle<br>Accidents</span>
    </li>
    <li class="program" style="top:625px">
      <svg viewBox="0 0 38 38" fill="none" stroke="#0b2410" stroke-width="1.6"><path d="M14 4h10v6H14zM13 13h11v6H13zM12 22h11v6H12zM11 31h11v5H11z"/><path d="M4 10l4 2M4 20l4 0M30 14l4-2M30 24l4 2"/></svg>
      <span><strong>Post-Operative Care</strong><br>Spine, Shoulder,<br>Knee, Total Joint<br>Replacement</span>
    </li>
    <li class="program" style="top:722px">
      <svg viewBox="0 0 38 38" fill="none" stroke="#0b2410" stroke-width="1.6"><circle cx="19" cy="10" r="6"/><path d="M10 36c0-9 4-14 9-14s9 5 9 14M19 16v6"/><circle cx="17" cy="20" r="2"/></svg>
      <span>Neck &amp; Back Pain</span>
    </li>
    <li class="program" style="top:766px">
      <svg viewBox="0 0 38 38" fill="none" stroke="#0b2410" stroke-width="1.6"><path d="M8 36V14c0-4 4-6 8-7h6c4 1 8 3 8 7v22M14 36V24M24 36V24"/><circle cx="19" cy="15" r="3"/></svg>
      <span>Shoulder Pain, Rotator<br>Cuff Injuries, Bursitis</span>
    </li>
    <li class="program" style="top:829px">
      <svg viewBox="0 0 38 38" fill="none" stroke="#0b2410" stroke-width="1.6"><path d="M14 2v20L5 30c-2 2 0 5 3 5h6l12-13V2"/><circle cx="20" cy="22" r="2"/><path d="M30 4l4 2M30 10h5M30 16l4-2"/></svg>
      <span>Hip, Knee, Ankle,<br>&amp; Foot Pain</span>
    </li>
  </ul>

  <div class="visit">
    <span class="visit-label">Visit us</span>
    <span class="visit-url">www.meadowlarkptrehab.com</span>
  </div>
</main>
</body>
</html>
```